Upmarket Dessert Lounge needs a Business Card Design

We are an upmarket dessert lounge needing a business card to match our image.

We want something that is simple yet beautiful, feminine, classy, sophisticated and elegant. We want it to stand out and don't mind if it is bold.

The design should include our logo and colours of red or maroon with gold highlights. We don't mind if black is used.

Marlow & Quince

Target Market(s)

For those who like to indulge or treat themselves and give in to their temptations on good quality desserts.

Industry/Entity Type

Business

Requirements
Must have
• Must include our logo and our name

Marlow & Quince

M & Q

```html
<!DOCTYPE html>
<html lang="en">
<head>
<meta charset="utf-8">
<title>Marlow &amp; Quince — Business Card</title>
<link rel="stylesheet" href="https://fonts.googleapis.com/css2?family=Open+Sans:wght@400;600&display=swap">
<style>
  :root {
    --backdrop: #f3e9e9;
    --maroon: #6a1b1e;
    --maroon-deep: #5a1518;
    --gold: #d9a66c;
    --gold-soft: #e8c08e;
    --peach: #f6cf97;
    --paper: #ffffff;
    --ink-light: #ffffff;
  }
  * { box-sizing: border-box; margin: 0; padding: 0; }
  html, body {
    width: 1200px;
    height: 951px;
    overflow: hidden;
    background: var(--backdrop);
    font-family: "Open Sans", Arial, sans-serif;
  }
  .canvas {
    position: relative;
    width: 1200px;
    height: 951px;
  }
  .card {
    position: absolute;
    width: 630px;
    height: 360px;
    border-radius: 22px;
    overflow: hidden;
    background: var(--maroon);
    box-shadow: 0 10px 24px rgba(90, 21, 24, 0.25);
  }

  /* Front */
  .card--front { left: 70px; top: 70px; }
  .front-ornament {
    position: absolute;
    right: 0; top: 0;
    width: 300px; height: 90px;
    background: radial-gradient(ellipse at 60% 20%, rgba(217,166,108,0.55), rgba(217,166,108,0) 70%);
  }
  .front-wordmark {
    position: absolute;
    left: 0; right: 0; top: 130px;
    text-align: center;
    color: var(--gold);
    font-weight: 400;
    font-size: 40px;
    letter-spacing: 3px;
    text-transform: uppercase;
  }
  .front-web {
    position: absolute;
    left: 0; right: 0; top: 268px;
    text-align: center;
    color: var(--ink-light);
    font-size: 18px;
    letter-spacing: 1.5px;
  }

  /* Back */
  .card--back { left: 500px; top: 520px; }
  .back-shape { position: absolute; inset: 0; }
  .back-ornament {
    position: absolute;
    left: 0; top: 0;
    width: 290px; height: 100px;
    background: radial-gradient(ellipse at 50% 15%, rgba(217,166,108,0.55), rgba(217,166,108,0) 70%);
  }
  .back-name {
    position: absolute;
    left: 40px; top: 118px;
    color: var(--ink-light);
    font-size: 26px;
    font-weight: 400;
  }
  .back-details {
    position: absolute;
    left: 40px; top: 222px;
    display: flex;
    gap: 36px;
    color: var(--ink-light);
    font-size: 15px;
    line-height: 1.3;
    font-style: normal;
  }
  .back-monogram {
    position: absolute;
    left: 450px; top: 110px;
    width: 170px;
    text-align: center;
    color: var(--maroon);
    font-size: 40px;
    font-weight: 600;
  }
</style>
</head>
<body>
<main class="canvas">

  <section class="card card--front" aria-label="Card front">
    <div class="front-ornament" role="img" aria-label="Gold floral flourish decoration"></div>
    <h1 class="front-wordmark">Marlow &amp; Quince</h1>
    <p class="front-web">www.marlowquince.com</p>
  </section>

  <section class="card card--back" aria-label="Card back">
    <svg class="back-shape" width="630" height="360" viewBox="0 0 630 360" aria-hidden="true">
      <path d="M468 0 C 420 90, 430 170, 455 240 C 475 300, 470 335, 458 360 L630 360 L630 0 Z" fill="var(--peach)"/>
      <path d="M482 0 C 436 90, 446 170, 470 240 C 490 300, 486 335, 474 360 L630 360 L630 0 Z" fill="var(--paper)"/>
    </svg>
    <div class="back-ornament" role="img" aria-label="Gold floral flourish decoration"></div>
    <h2 class="back-name">Marlow &amp; Quince</h2>
    <div class="back-details">
      <address class="back-address">
        1480 Velvet Row<br>
        Suite 204-118<br>
        Alderbrook, TX 78415
      </address>
      <p class="back-contact">
        512-555-0143<br>
        512-555-0144<br>
        hello@marlowquince.com<br>
        www.marlowquince.com
      </p>
    </div>
    <p class="back-monogram">M &amp; Q</p>
  </section>

</main>
</body>
</html>
```